Banner & also another minor digital image for an Online Academic Journal

A direct example of what I need can be found in this webpage: http://openfolio.kestrelvale.edu/qrmt/
(Please see attached files, "sAMPLE", and "sAMPLE 2", so you can see what I mean.)
This link (http://openfolio.kestrelvale.edu/qrmt/) is for an existing ONLINE ACADEMIC JOURNAL at the Harrowgate Institute of Letters.
It will help for you to be acquainted with the format of Online Academic Journals.
You will find that there is a banner on top as well as a digital image of a journal/book cover on the right.
I need a
(1) banner and
a (2) digital journal/book cover
for a website for an ONLINE ACADEMIC JOURNAL.
I am looking for a serious, professional, elegant design.
There will not be a print version. Only web-based online publication. No coding needed, only PSD, JPG/PNG and PDF.
1) We use QuillNest (http://openfolio.quillnest.com/archive-platform/periodicals/) for the digital image of the journal/book cover layout. Link shows the general layout of the journal website.
2) For the digital image of the journal/book cover and also the banner,
Name of the journal is....
"Solace: A Review on Coercion and Abuse Studies"
Only this text will be used and applied to both banner and cover.
***The color associated with the theme of dignity is purple
****You could also add the color red.
*****I don't want the design to be garish, but accents in red might represent
the sexual exploitation and violence in the title.
3) Attached "sAmple 2" file is a basic design for the digital image of the journal/book cover from QuillNest. I am looking for something more elegant and professional looking. Your creativity is encouraged. I am open to receiving your interpretation.
Target Market(s)
Academics & Community Professionals
Industry/Entity Type
Non Profit
Match journal design

```html
<!DOCTYPE html>
<html lang="en">
<head>
<meta charset="utf-8">
<title>Solace: A Review on Coercion and Abuse Studies</title>
<link rel="stylesheet" href="https://fonts.googleapis.com/css2?family=Cinzel:wght@400;500&display=swap">
<style>
  :root {
    --stage-light: #9c97ab;
    --stage-dark: #625a80;
    --silk-deep: #3d2462;
    --silk-mid: #6a4c9c;
    --silk-light: #b4a6e0;
    --silk-glow: #d7cdf4;
    --cover-panel: #8a6aae;
    --ink: #ffffff;
    --rule: rgba(255, 255, 255, 0.85);
  }
  * { box-sizing: border-box; margin: 0; padding: 0; }
  html, body { width: 1200px; height: 600px; overflow: hidden; }
  body {
    position: relative;
    background: radial-gradient(ellipse 70% 80% at 50% 50%, var(--stage-light), var(--stage-dark));
    font-family: "Cinzel", "Times New Roman", serif;
    color: var(--ink);
  }

  /* Web banner */
  .banner {
    position: absolute;
    left: 10px; top: 53px;
    width: 1180px; height: 139px;
    overflow: hidden;
    box-shadow: 0 1px 3px rgba(40, 20, 70, 0.4);
  }
  .banner__silk {
    position: absolute; inset: 0;
    background:
      linear-gradient(175deg, transparent 30%, rgba(215, 205, 244, 0.45) 45%, transparent 60%),
      linear-gradient(180deg, var(--silk-mid) 0%, var(--silk-light) 38%, var(--silk-deep) 62%, var(--silk-mid) 80%, var(--silk-deep) 100%);
  }
  .banner__title {
    position: absolute;
    left: 92px; top: 28px;
    font-size: 68px;
    font-weight: 500;
    line-height: 1;
    letter-spacing: 1px;
    text-shadow: 0 1px 3px rgba(30, 10, 60, 0.5);
  }
  .banner__rule {
    position: absolute;
    left: 0; top: 106px;
    width: 434px; height: 2px;
    background: var(--rule);
  }
  .banner__subtitle {
    position: absolute;
    left: 900px; top: 40px;
    font-size: 18px;
    line-height: 21.5px;
    letter-spacing: 0.4px;
  }

  /* Journal cover */
  .cover {
    position: absolute;
    left: 474px; top: 214px;
    width: 252px; height: 362px;
    overflow: hidden;
    box-shadow: 0 1px 4px rgba(40, 20, 70, 0.4);
  }
  .cover__silk {
    position: absolute;
    left: 0; top: 0;
    width: 100%; height: 228px;
    background:
      linear-gradient(165deg, transparent 35%, rgba(215, 205, 244, 0.5) 55%, transparent 72%),
      linear-gradient(180deg, var(--silk-light) 0%, var(--silk-mid) 25%, var(--silk-deep) 40%, var(--silk-glow) 68%, var(--silk-light) 100%);
  }
  .cover__title {
    position: absolute;
    left: 31px; top: 106px;
    font-size: 34px;
    font-weight: 500;
    line-height: 1;
    text-shadow: 0 1px 2px rgba(30, 10, 60, 0.5);
  }
  .cover__panel {
    position: absolute;
    left: 0; top: 228px;
    width: 100%; height: 134px;
    background: var(--cover-panel);
  }
  .cover__subtitle {
    position: absolute;
    left: 30px; top: 30px;
    font-size: 15px;
    line-height: 19px;
    letter-spacing: 0.3px;
  }
</style>
</head>
<body>
  <header class="banner">
    <div class="banner__silk" role="img" aria-label="Flowing violet silk background"></div>
    <h1 class="banner__title">Solace</h1>
    <div class="banner__rule"></div>
    <p class="banner__subtitle">A Review on<br>Coercion and Abuse<br>Studies</p>
  </header>

  <section class="cover" aria-label="Journal cover">
    <div class="cover__silk" role="img" aria-label="Flowing violet silk background"></div>
    <h2 class="cover__title">Solace</h2>
    <div class="cover__panel">
      <p class="cover__subtitle">A Review on<br>Coercion and Abuse<br>Studies</p>
    </div>
  </section>
</body>
</html>
```